Membership Based Medical Practice Website

We need a functioning website for a new Membership based medical practice. There will be an enrollment fee and a monthly fee. We would like to see designs that are modern, simple. Should use neutral light colors. Examples of sites we like are www.kellanmoorclinic.com and https://fernholtcare.com/ We also have a link that when "Join Now" is clicked it will go to the signup website.

Target Market(s)

Gay Men, local population, Age group 20 to 60's.

Industry/Entity Type

Medical

Coding

Coded - Design and coding required

Number of Pages Required

5+ page

Font styles to use
Sans Serif

Colors
ffffff
cee9f5
ecf7fb
cfeae6
edf8f6
aaaaaa
e9e9e9
dbdbdb
fff3d1

Requirements
Must have
• Logo and header on every page. Clean, simple design, clear content, mobile compatible.
• Must use Wordpress
Nice to have
• Ideas should come from kellanmoorclinic.com
• Easy to read
Should not have
• Generic patient pictures, bold colors.
• Should not copy from above websites.

```html
<!DOCTYPE html>
<html lang="en">
<head>
<meta charset="utf-8">
<title>About Us – Larkfield Infectious Disease Specialists</title>
<link href="https://fonts.googleapis.com/css2?family=Lato:wght@400;700&display=swap" rel="stylesheet">
<style>
  :root {
    --white: #ffffff;
    --section-bg: #e6f3f9;
    --mint: #cfeae6;
    --cream: #fff3d1;
    --accent: #2a9fd6;
    --ink: #222222;
    --muted: #444444;
    --hero-dark: #3b4438;
    --hero-mid: #6b7a5c;
    --hero-sky: #b9bcc2;
    --brand: #b8934a;
  }
  * { box-sizing: border-box; margin: 0; padding: 0; }
  html, body { width: 994px; height: 1200px; overflow: hidden; }
  body { font-family: "Lato", sans-serif; color: var(--ink); background: var(--white); position: relative; }

  .site-header { position: absolute; top: 0; left: 0; width: 994px; height: 118px; background: var(--white); }
  .brand { position: absolute; left: 60px; top: 34px; display: flex; align-items: center; gap: 10px; }
  .brand-dot { width: 38px; height: 38px; border-radius: 50%; border: 2px solid var(--brand); }
  .brand-name { font-size: 13px; line-height: 1.35; letter-spacing: 0.5px; color: var(--brand); font-weight: 400; }
  .main-nav { position: absolute; top: 54px; left: 367px; display: flex; align-items: center; }
  .main-nav a { font-size: 12px; font-weight: 700; color: var(--ink); text-decoration: none; margin-right: 35px; letter-spacing: 0.2px; }
  .main-nav .join-btn { position: absolute; left: 466px; top: -8px; width: 99px; height: 35px; border-radius: 18px; background: var(--mint); display: flex; align-items: center; justify-content: center; font-size: 13px; margin: 0; letter-spacing: 0.6px; }

  .hero { position: absolute; top: 118px; left: 0; width: 994px; height: 155px;
    background: linear-gradient(180deg, var(--hero-sky) 0%, #8a9184 30%, var(--hero-mid) 55%, var(--hero-dark) 100%);
    display: flex; align-items: center; justify-content: center; }
  .hero h1 { color: var(--white); font-size: 35px; font-weight: 700; margin-top: -22px; }

  .about { position: absolute; top: 273px; left: 0; width: 994px; height: 797px; background: var(--section-bg); }
  .about-title { position: absolute; left: 61px; top: 51px; font-size: 28px; font-weight: 400; color: #333; }
  .about-intro { position: absolute; left: 61px; top: 107px; font-size: 12.5px; color: var(--ink); }

  .topic { position: absolute; left: 62px; width: 870px; }
  .topic-philosophy { top: 144px; }
  .topic-meet { top: 565px; }
  .topic-icon { position: absolute; left: 0; top: 0; width: 50px; height: 50px; border-radius: 50%; border: 2px solid var(--accent); background: var(--cream); display: flex; align-items: center; justify-content: center; }
  .topic-title { position: absolute; left: 62px; top: 14px; font-size: 15.5px; font-weight: 700; color: var(--accent); }
  .topic-body { position: absolute; left: 63px; top: 52px; width: 810px; }
  .topic-body p { font-size: 12.4px; line-height: 24.5px; color: var(--ink); margin-bottom: 10px; }

  .site-footer { position: absolute; top: 1070px; left: 0; width: 994px; height: 130px; background: var(--white); text-align: center; }
  .footer-nav { padding-top: 32px; display: flex; justify-content: center; gap: 35px; }
  .footer-nav a { font-size: 12px; font-weight: 700; color: var(--ink); text-decoration: none; }
  .copyright { margin-top: 12px; font-size: 10.5px; color: var(--muted); }
  .social { margin-top: 14px; display: flex; justify-content: center; gap: 16px; }
  .social span { width: 16px; height: 16px; border-radius: 50%; background: #666; display: block; }
</style>
</head>
<body>
  <header class="site-header">
    <div class="brand">
      <span class="brand-dot"></span>
      <span class="brand-name">LARKFIELD<br>Infectious Disease Specialists</span>
    </div>
    <nav class="main-nav">
      <a href="#">HOME</a>
      <a href="#">SPECIALTIES</a>
      <a href="#">PRICING</a>
      <a href="#">ABOUT US</a>
      <a href="#">FAQ</a>
      <a href="#">BLOG</a>
      <a href="#" class="join-btn">JOIN US</a>
    </nav>
  </header>

  <section class="hero" role="img" aria-label="Photo of a quiet country road through green pasture under a grey sky">
    <h1>About us</h1>
  </section>

  <main class="about">
    <h2 class="about-title">About Us</h2>
    <p class="about-intro">We are a clinic focused on the physician-patient relationship, and focused on your well-being</p>

    <section class="topic topic-philosophy">
      <div class="topic-icon">
        <svg width="18" height="20" viewBox="0 0 18 20" aria-hidden="true">
          <path d="M1 0h11l5 5v15H1z" fill="#222"/>
          <path d="M12 0v5h5" fill="#555"/>
          <rect x="4.5" y="9" width="9" height="1.6" fill="var(--cream)"/>
          <rect x="4.5" y="12" width="9" height="1.6" fill="var(--cream)"/>
          <rect x="4.5" y="15" width="9" height="1.6" fill="var(--cream)"/>
        </svg>
      </div>
      <h3 class="topic-title">Our Philosophy</h3>
      <div class="topic-body">
        <p>Our goal is to build and maintain a strong doctor-patient relationship so we can address your needs in real time. We will spend time with our patients to understand you, your medical background and needs, and to establish preventative plans to keep you healthy and/or develop further treatment options to get you on a path to wellness. The direct care provider method puts you back in charge of your health, with the cooperation and guidance of your doctor.</p>
        <p>It is our goal to provide a supportive and safe environment, free of judgement. We understand that your time is valuable. It is easy to speak with Dr. Moreau either online or by phone. Follow-up visits are available by video chat, so that you don’t have to leave work or find transportation to see your doctor.</p>
        <p>Healthcare is expensive, and it is often difficult to find out in advance how much you will be charged. Since our clinic does not bill insurance companies, but rather contracts directly with each patient, you will know the exact price of each visit. Also we offer highly discounted rates on blood tests and medications for members.</p>
        <p>We make sure that there is enough time to hear your story, devise a plan tailored to your situation, and thoroughly answer all your questions. We arrange our schedule to minimize any time spent in the waiting room. We limit the number of patients we see so that we never have to rush through your appointment.</p>
      </div>
    </section>

    <section class="topic topic-meet">
      <div class="topic-icon">
        <svg width="24" height="20" viewBox="0 0 24 20" aria-hidden="true">
          <circle cx="5" cy="5" r="3" fill="#222"/>
          <circle cx="19" cy="5" r="3" fill="#222"/>
          <circle cx="12" cy="6" r="4" fill="#222"/>
          <path d="M0 16c0-4 2-6 5-6s4 1 4 2H0z" fill="#222"/>
          <path d="M24 16c0-4-2-6-5-6s-4 1-4 2h9z" fill="#222"/>
          <path d="M5 19c0-5 3-8 7-8s7 3 7 8z" fill="#222"/>
        </svg>
      </div>
      <h3 class="topic-title">Meet Us</h3>
      <div class="topic-body">
        <p>Dr. Moreau grew up in New York until her family relocated to Seoul when she was 9. She graduated medical school at Hanbit Medical University in South Korea, then went into internal medicine residency at Great Lakes State University in Lansing, MI. She then went to Gulf Coast University Medical Branch in Galveston Texas for Infectious Diseases training. She decided to come back to the mid-west and has been practicing Infectious Disease in Northern Indiana since 2013. Dr. Moreau is board certified in both Infectious Diseases and Internal medicine. She is a member of Infectious Care Society of America (ICSA) and American Institute of Lifestyle Health (AILH).</p>
      </div>
    </section>
  </main>

  <footer class="site-footer">
    <nav class="footer-nav">
      <a href="#">HOME</a>
      <a href="#">SPECIALTIES</a>
      <a href="#">PRICING</a>
      <a href="#">ABOUT US</a>
      <a href="#">FAQ</a>
      <a href="#">BLOG</a>
    </nav>
    <p class="copyright">Copyright © 2019 CompanyName All Rights Reserved.</p>
    <div class="social" aria-label="Social links">
      <span></span><span></span><span></span><span></span><span></span>
    </div>
  </footer>
</body>
</html>
```